Redesign of business card for Cedar Ridge Mechanical

We are looking for a new design for our business cards for Cedar Ridge Mechanical. We are a plumbing & HVAC construction company, operating on the West Coast of Canada and USA. Logo attached.
Industry/Entity Type
Construction - Plumbing & HVAC
Contact Information for Business Card
Name, address, phone numbers, email, website address
Look and feel
Each slider illustrates characteristics of the customer's brand and the style your logo design should communicate.

```html
<!DOCTYPE html>
<html lang="en">
<head>
<meta charset="utf-8">
<title>Cedar Ridge Mechanical – Business Card</title>
<link href="https://fonts.googleapis.com/css2?family=Montserrat:wght@400;500;700&display=swap" rel="stylesheet">
<style>
  :root {
    --bg: #1d1d1d;
    --card-white: #ffffff;
    --card-black: #141414;
    --card-black-soft: #262626;
    --stripe-grey: #9a9a9a;
    --text-light: #f2f2f2;
    --text-muted: #bdbdbd;
    --text-dark: #141414;
  }
  * { box-sizing: border-box; margin: 0; padding: 0; }
  html, body { width: 1200px; height: 801px; overflow: hidden; }
  body {
    background: var(--bg);
    font-family: "Montserrat", sans-serif;
    display: flex;
    align-items: center;
    justify-content: center;
    gap: 60px;
  }
  .card {
    position: relative;
    width: 520px;
    height: 300px;
    border-radius: 22px;
    overflow: hidden;
  }
  /* Front */
  .card--front { background: var(--card-white); }
  .card__swoosh { position: absolute; inset: 0; width: 100%; height: 100%; }
  .brand {
    position: absolute;
    display: flex;
    align-items: center;
    gap: 12px;
    font-weight: 700;
    text-transform: uppercase;
    letter-spacing: 1px;
  }
  .brand__mark { display: block; border-radius: 3px; }
  .card--front .brand {
    top: 48px; left: 0; right: 0;
    justify-content: center;
    color: var(--text-dark);
    font-size: 22px;
  }
  .card--front .brand__mark { width: 22px; height: 22px; background: var(--text-dark); }
  .person {
    position: absolute;
    left: 36px; top: 180px;
    color: var(--text-light);
    text-align: right;
    width: 150px;
  }
  .person__name { font-weight: 700; font-size: 17px; letter-spacing: 0.5px; }
  .person__role { font-size: 12px; color: var(--text-muted); margin-top: 3px; }
  .divider {
    position: absolute;
    left: 202px; top: 170px;
    width: 1px; height: 62px;
    background: var(--stripe-grey);
  }
  .contact {
    position: absolute;
    left: 218px; top: 168px;
    list-style: none;
    color: var(--text-light);
    font-size: 13px;
  }
  .contact li { display: flex; align-items: center; gap: 8px; height: 22px; }
  .contact svg { width: 13px; height: 13px; fill: var(--text-light); flex: none; }
  .address {
    position: absolute;
    left: 0; right: 0; top: 252px;
    text-align: center;
    color: var(--text-light);
    font-size: 13px;
  }
  /* Back */
  .card--back {
    background: linear-gradient(135deg, var(--card-black-soft) 0%, var(--card-black) 55%, #202020 100%);
  }
  .card--back .brand {
    inset: 0;
    justify-content: center;
    color: var(--text-light);
    font-size: 26px;
  }
  .card--back .brand__mark { width: 26px; height: 26px; background: var(--text-light); }
</style>
</head>
<body>
  <article class="card card--front">
    <svg class="card__swoosh" viewBox="0 0 520 300" preserveAspectRatio="none" aria-hidden="true">
      <path d="M0 190 Q 220 150 520 95 L520 300 L0 300 Z" fill="#9a9a9a"/>
      <path d="M0 200 Q 220 160 520 107 L520 300 L0 300 Z" fill="#ffffff"/>
      <path d="M0 212 Q 220 172 520 118 L520 300 L0 300 Z" fill="#141414"/>
      <path d="M0 150 Q 230 135 520 108 L520 300 L0 300 Z" fill="#141414"/>
    </svg>
    <div class="brand"><span class="brand__mark"></span>Cedar Ridge Mechanical</div>
    <div class="person">
      <div class="person__name">DANIEL HAYES</div>
      <div class="person__role">Manager</div>
    </div>
    <div class="divider"></div>
    <ul class="contact">
      <li><svg viewBox="0 0 24 24"><path d="M6.6 10.8a15 15 0 0 0 6.6 6.6l2.2-2.2a1 1 0 0 1 1-.25 11.4 11.4 0 0 0 3.6.57 1 1 0 0 1 1 1V20a1 1 0 0 1-1 1A17 17 0 0 1 3 4a1 1 0 0 1 1-1h3.5a1 1 0 0 1 1 1c0 1.25.2 2.45.57 3.6a1 1 0 0 1-.25 1z"/></svg>555-014-2100</li>
      <li><svg viewBox="0 0 24 24"><path d="M2 5h20v14H2z M4 7v.5l8 5 8-5V7l-8 5z" fill-rule="evenodd"/></svg>hello@cedarridgemech.com</li>
      <li><svg viewBox="0 0 24 24"><circle cx="12" cy="12" r="10"/></svg>www.cedarridgemech.com</li>
    </ul>
    <div class="address">Your address, city, state, ZIP 0000</div>
  </article>

  <article class="card card--back">
    <div class="brand"><span class="brand__mark"></span>Cedar Ridge Mechanical</div>
  </article>
</body>
</html>
```